Kor'v Meridell Travel

We need a sleek, professional, inviting card to elicit global travel for the experienced and professional traveler. Royal blue, black and silver. (perhaps the wording could be silver with black shadow?-get creative) Maybe a watermark on the front and the full raised logo on the back.
We want a stylish and modern card, but professional.

```html
<!DOCTYPE html>
<html lang="en">
<head>
<meta charset="utf-8">
<title>Kor'v Meridell Travel — Business Card</title>
<link href="https://fonts.googleapis.com/css2?family=Open+Sans:ital,wght@0,400;0,600;0,700;1,400&display=swap" rel="stylesheet">
<style>
  :root {
    --backdrop: #2b2b2d;
    --card: #1e1e20;
    --royal-blue: #1f9be0;
    --leaf-green: #7cc242;
    --text-grey: #c9c9cc;
    --muted-grey: #a3a3a8;
    --silver: #b9bcc2;
  }
  * { margin: 0; padding: 0; box-sizing: border-box; }
  html, body {
    width: 1200px; height: 900px; overflow: hidden;
    background: var(--backdrop);
    font-family: "Open Sans", Arial, sans-serif;
  }
  .sheet {
    width: 1200px; height: 900px;
    display: flex; flex-direction: column;
    align-items: center; justify-content: center; gap: 50px;
  }
  .card {
    width: 660px; height: 377px;
    background: var(--card);
    box-shadow: 0 14px 30px rgba(0,0,0,0.45);
    position: relative;
  }
  /* Front */
  .card--front { display: flex; align-items: center; }
  .identity {
    width: 300px; text-align: right; padding-right: 26px;
  }
  .identity__name {
    color: var(--royal-blue); font-weight: 700; font-size: 27px;
    text-transform: uppercase; letter-spacing: -0.2px; line-height: 1.1;
  }
  .identity__role {
    color: var(--muted-grey); font-style: italic; font-size: 19px; margin-top: 4px;
  }
  .divider {
    width: 1.5px; height: 118px; background: var(--royal-blue);
  }
  .contact {
    list-style: none; padding-left: 24px;
    color: var(--text-grey); font-size: 17px; line-height: 1.32;
  }
  .contact__item { display: flex; align-items: flex-start; gap: 8px; }
  .contact__icon { width: 14px; height: 14px; margin-top: 4px; flex: none; fill: var(--leaf-green); }
  .contact__indent { padding-left: 22px; }
  /* Back */
  .card--back { display: flex; align-items: center; justify-content: center; gap: 16px; }
  .brand__dot {
    width: 18px; height: 18px; border-radius: 50%; background: var(--silver);
  }
  .brand__name {
    color: var(--silver); font-weight: 600; font-size: 34px;
    text-transform: uppercase; letter-spacing: 3px;
  }
</style>
</head>
<body>
<main class="sheet">
  <section class="card card--front" aria-label="Card front">
    <div class="identity">
      <p class="identity__name">Dane Holloway</p>
      <p class="identity__role">President</p>
    </div>
    <div class="divider"></div>
    <ul class="contact">
      <li class="contact__item">
        <svg class="contact__icon" viewBox="0 0 14 14" aria-hidden="true"><path d="M7 0a5 5 0 0 0-5 5c0 3.6 5 9 5 9s5-5.4 5-9a5 5 0 0 0-5-5zm0 7a2 2 0 1 1 0-4 2 2 0 0 1 0 4z"/></svg>
        <span>18740 Coral Bay Harbor</span>
      </li>
      <li class="contact__item contact__indent">Coral Bay CA 90417</li>
      <li class="contact__item">
        <svg class="contact__icon" viewBox="0 0 14 14" aria-hidden="true"><path d="M3 1l2 0 1.3 3.2-1.6 1.1a8 8 0 0 0 4 4l1.1-1.6L13 9v2a2 2 0 0 1-2 2A10 10 0 0 1 1 3a2 2 0 0 1 2-2z"/></svg>
        <span>555-310-7428</span>
      </li>
      <li class="contact__item">
        <svg class="contact__icon" viewBox="0 0 14 14" aria-hidden="true"><path d="M1 3h12v8H1z M1 3l6 4.5L13 3" stroke="#1e1e20" stroke-width="1"/></svg>
        <span>info@korvmeridell.com</span>
      </li>
      <li class="contact__item">
        <svg class="contact__icon" viewBox="0 0 14 14" aria-hidden="true"><circle cx="7" cy="7" r="6"/><path d="M1 7h12M7 1c-2.5 3-2.5 9 0 12M7 1c2.5 3 2.5 9 0 12" stroke="#1e1e20" stroke-width="1" fill="none"/></svg>
        <span>www.korvmeridell.com</span>
      </li>
    </ul>
  </section>

  <section class="card card--back" aria-label="Card back">
    <span class="brand__dot" aria-hidden="true"></span>
    <p class="brand__name">Kor'v Meridell Travel</p>
  </section>
</main>
</body>
</html>
```